Defense Attorney Business Card Design Project/ Stationary

I am looking for a distinctive business card design for my solo law practice.
I practice criminal defense, both juvenile and adult, including DUI. I am a very experienced attorney with prior military experience. The design should convey a traditional, old school flair, but not be too stodgy or uptight. Some color. My logo should appear.
Updates

Project Deadline Extended Reason: I misunderstood how this project works and I was not prepared with my logo when this project ran the first time. Added Thursday, November 13, 2014

Project Deadline Extended
Reason: I was sent overseas on military duty last year, which interrupted this project. Thank you for your participation... I hope we can get this done this week! Thank you, Neil

Target Market(s)

Regular everyday people looking for strong, knowledgeable, authoritative representation while they are faced with criminal charges. Many have never been charged with a crime before. A reassuring air is therefore desired.

Industry/Entity Type

Business

Contact Information for Business Card

My information is:
Theodore M. Quill, Attorney at Law
785 Birch Avenue Suite 300
Oakland, California 94719
Tel: (510) 384-6125
Fax: (510) 391-7802
email: neilquilllaw@mailvine.example
web: www.neilquilllaw.example

Font styles to use
Serif
Sans Serif
Decorative

Colors
0255a3
ffffff

Requirements
Must have
• Sharp lines, bold elements. Conservative use of colors, such as deep blues, burgundy, grays for example.
• While my logo says "Neil Quill", it should be modified to show "Theodore M. Quill".
Should not have
• Cliche imagery such as scales of justice, gavels, Statue of Liberty, etc.

```html
<!DOCTYPE html>
<html lang="en">
<head>
<meta charset="utf-8">
<title>Theodore M. Quill Law — Business Card</title>
<link rel="stylesheet" href="https://fonts.googleapis.com/css2?family=Cinzel:wght@400;600&family=Crimson+Pro:wght@400;500&display=swap">
<style>
  :root {
    --page: #e9e7e3;
    --cream: #e9d79f;
    --cream-line: #f3e6b9;
    --ink-blue: #1f4f9e;
    --brand-blue: #0255a3;
    --gold: #ecd9a0;
    --shadow: rgba(0, 0, 0, 0.18);
  }
  * { box-sizing: border-box; margin: 0; padding: 0; }
  html, body {
    width: 1200px; height: 1000px; overflow: hidden;
    background: var(--page);
  }
  .sheet {
    width: 1200px; height: 1000px;
    display: flex; flex-direction: column;
    align-items: center; justify-content: center; gap: 60px;
  }
  .card {
    position: relative;
    width: 700px; height: 400px;
    box-shadow: 0 10px 28px var(--shadow);
    overflow: hidden;
  }

  /* Front */
  .card--front { background: var(--cream); color: var(--ink-blue); }
  .edge-stripes {
    position: absolute; top: 0; bottom: 0; width: 42px;
    display: flex; justify-content: space-between;
  }
  .edge-stripes span { width: 3px; background: var(--cream-line); }
  .edge-stripes--left { left: 26px; }
  .edge-stripes--right { right: 26px; }

  .front-content {
    position: absolute; inset: 38px 90px 30px 90px;
    display: flex; flex-direction: column; align-items: center;
  }
  .lockup {
    align-self: flex-end; margin-right: 24px;
    display: flex; flex-direction: column; align-items: flex-start;
  }
  .lockup__name {
    font-family: "Cinzel", serif; font-weight: 600;
    font-size: 24px; letter-spacing: 0.5px; color: var(--ink-blue);
    display: flex; align-items: center; gap: 10px;
  }
  .lockup__dot {
    width: 12px; height: 12px; border-radius: 50%; background: var(--ink-blue);
  }
  .lockup__rule {
    width: 100%; height: 1px; background: var(--ink-blue); margin: 4px 0 4px;
  }
  .lockup__tagline {
    font-family: "Crimson Pro", serif; font-size: 12px;
    letter-spacing: 1.5px; text-transform: uppercase; padding-left: 40px;
  }
  .attorney-name {
    margin-top: 46px;
    font-family: "Cinzel", serif; font-weight: 400;
    font-size: 32px; letter-spacing: 1px; color: var(--ink-blue);
  }
  .contact {
    margin-top: 22px; text-align: center;
    font-family: "Crimson Pro", serif; font-size: 17px; line-height: 1.45;
  }
  .contact__row--spaced { margin-top: 8px; }

  /* Back */
  .card--back { background: var(--brand-blue); color: var(--gold); }
  .back-lockup {
    position: absolute; left: 80px; right: 80px; top: 130px;
    display: flex; flex-direction: column;
  }
  .back-lockup__name {
    font-family: "Cinzel", serif; font-weight: 600;
    font-size: 42px; letter-spacing: 1px;
    display: flex; align-items: center; justify-content: space-between;
  }
  .back-lockup__dot {
    width: 22px; height: 22px; border-radius: 50%; background: var(--gold);
  }
  .back-lockup__rule {
    height: 1px; background: var(--gold); margin: 8px 0 10px;
  }
  .back-lockup__tagline {
    font-family: "Crimson Pro", serif; font-size: 17px;
    letter-spacing: 2px; text-transform: uppercase; padding-left: 70px;
  }
</style>
</head>
<body>
<main class="sheet">

  <section class="card card--front" aria-label="Business card front">
    <div class="edge-stripes edge-stripes--left"><span></span><span></span><span></span></div>
    <div class="edge-stripes edge-stripes--right"><span></span><span></span><span></span></div>

    <div class="front-content">
      <div class="lockup">
        <div class="lockup__name"><span class="lockup__dot"></span>Theodore M. Quill Law</div>
        <div class="lockup__rule"></div>
        <div class="lockup__tagline">DUI · Criminal Defense · 785</div>
      </div>

      <h1 class="attorney-name">Theodore M. Quill, Attorney</h1>

      <address class="contact" style="font-style: normal;">
        <div class="contact__row">785 Birch Avenue Suite 300</div>
        <div class="contact__row">Oakland, California 94719</div>
        <div class="contact__row contact__row--spaced">Tel: (510) 384-6125 &nbsp;Fax: (510) 391-7802</div>
        <div class="contact__row">Email: neilquilllaw@mailvine.example &nbsp;Web: www.neilquilllaw.example</div>
      </address>
    </div>
  </section>

  <section class="card card--back" aria-label="Business card back">
    <div class="back-lockup">
      <div class="back-lockup__name">Theodore M. Quill Law <span class="back-lockup__dot"></span></div>
      <div class="back-lockup__rule"></div>
      <div class="back-lockup__tagline">DUI · Criminal Defense · 785</div>
    </div>
  </section>

</main>
</body>
</html>
```